Tradelume.ai

Australian based application building technology company. website (tradelume.ai) servicing the retail and shopping industries, IoT
Similar services to https://vextrio.com/.
Logo attached

Target Market(s)

Technology Retail

Industry/Entity Type

It Company

Number of Pages Required

2 page

Font styles to use
Other font styles liked:
• We will supply

Colors
ec1f27

Requirements
Must have
• responsive, extra small, small, medium, large, wide
Nice to have
• Modern, sophisticated, current and ON trende
Should not have
• Over saturation, keep it simple, smart and easy navigation

```html
<!DOCTYPE html>
<html lang="en">
<head>
<meta charset="utf-8">
<title>Tradelume</title>
<link href="https://fonts.googleapis.com/css2?family=Lato:wght@300;400;700;900&family=Roboto:wght@400;500;700&family=Playfair+Display:wght@700&display=swap" rel="stylesheet">
<style>
  :root {
    --brand-red: #ec1f27;
    --screen-red: #b5121b;
    --ink: #222222;
    --body-text: #555555;
    --light-grey: #f1f1f1;
    --white: #ffffff;
    --rule: #333333;
    --hero-dark: #1d1a19;
    --hero-warm: #6a5446;
    --device-black: #1b1b1b;
    --device-edge: #3a3a3a;
    --device-silver: #e4e4e6;
  }
  * { box-sizing: border-box; margin: 0; padding: 0; }
  html, body { width: 1200px; height: 3000px; overflow: hidden; }
  body { position: relative; background: var(--white); font-family: "Roboto", Arial, sans-serif; color: var(--ink); }
  .abs { position: absolute; }
  .center { text-align: center; }

  /* Header + hero */
  .hero { left: 0; top: 0; width: 1200px; height: 648px; background:
      radial-gradient(ellipse 260px 220px at 800px 430px, #8a6a55 0%, rgba(138,106,85,0) 100%),
      radial-gradient(ellipse at 72% 35%, var(--hero-warm) 0%, #3a302b 42%, var(--hero-dark) 85%); }
  .brand { display: flex; align-items: center; gap: 14px; font-family: "Lato", Arial, sans-serif; font-weight: 400; font-size: 30px; letter-spacing: 1px; }
  .brand-mark { width: 40px; height: 40px; border-radius: 50%; }
  .brand--light { left: 100px; top: 40px; color: var(--white); }
  .brand--light .brand-mark { background: var(--white); }
  .main-nav { left: 458px; top: 50px; display: flex; gap: 42px; font-size: 17px; color: var(--white); text-transform: uppercase; line-height: 24px; }
  .btn-ghost-light { left: 948px; top: 34px; width: 152px; height: 54px; border: 2px solid var(--white); border-radius: 27px; color: var(--white); font-size: 16px; font-weight: 500; display: flex; align-items: center; justify-content: center; }
  .hero-title { left: 100px; top: 200px; font-family: "Lato", Arial, sans-serif; font-weight: 900; font-size: 56px; color: var(--white); letter-spacing: 1px; line-height: 70px; }
  .hero-lede { left: 100px; top: 286px; width: 420px; font-size: 18px; line-height: 30px; color: var(--white); }
  .btn-solid { background: var(--brand-red); color: var(--white); border-radius: 28px; display: flex; align-items: center; justify-content: center; font-weight: 500; text-transform: uppercase; }
  .hero-cta { left: 100px; top: 372px; width: 178px; height: 54px; font-size: 20px; border: 2px solid var(--white); }
  .hero-arrows { left: 100px; top: 464px; }

  /* Devices */
  .device { border-radius: 18px; background: var(--device-black); box-shadow: inset 0 0 0 3px var(--device-edge), 0 8px 20px rgba(0,0,0,0.25); }
  .device--silver { background: var(--device-silver); box-shadow: inset 0 0 0 2px #cfcfd2, 0 6px 16px rgba(0,0,0,0.15); border-radius: 30px 30px 0 0; }
  .screen { overflow: hidden; background: var(--white); }
  .hero-phone { left: 696px; top: 132px; width: 236px; height: 488px; border-radius: 38px; }
  .hero-screen { left: 706px; top: 188px; width: 216px; height: 376px; }
  .hero-screen-name { left: 706px; top: 338px; width: 216px; font-family: "Lato", Arial, sans-serif; font-weight: 400; font-size: 31px; color: var(--brand-red); letter-spacing: 0.5px; }
  .hero-screen-copy { left: 706px; top: 414px; width: 216px; font-size: 16px; font-weight: 500; line-height: 29px; color: var(--ink); }

  /* Intro section */
  .trio-left { left: 112px; top: 744px; width: 148px; height: 336px; }
  .trio-left-screen { left: 120px; top: 786px; width: 132px; height: 254px; background: linear-gradient(160deg, #eef1f4 0%, #d9dde2 55%, #f2d8b8 100%); }
  .trio-right { left: 440px; top: 744px; width: 144px; height: 336px; }
  .trio-right-screen { left: 448px; top: 780px; width: 128px; height: 264px; }
  .trio-car { left: 458px; top: 806px; width: 108px; height: 50px; background: linear-gradient(180deg, #e9e9ec, #b9bcc2); border-radius: 10px; }
  .trio-right-name { left: 448px; top: 876px; width: 128px; font-family: "Lato", Arial, sans-serif; font-size: 25px; color: var(--brand-red); }
  .trio-right-copy { left: 456px; top: 936px; width: 112px; font-size: 10px; font-weight: 700; line-height: 19px; color: var(--ink); }
  .trio-center { left: 264px; top: 724px; width: 176px; height: 372px; background: #15202b; }
  .trio-center-screen { left: 272px; top: 762px; width: 160px; height: 302px; background: var(--screen-red); }
  .trio-center-small { left: 272px; width: 160px; font-size: 9px; line-height: 13px; color: #ffd9da; }
  .trio-center-name { left: 272px; top: 940px; width: 160px; font-family: "Lato", Arial, sans-serif; font-size: 34px; color: var(--white); }

  .section-heading { font-family: "Lato", Arial, sans-serif; font-weight: 700; font-size: 26px; line-height: 38px; color: var(--ink); }
  .section-copy { font-size: 13px; line-height: 24px; color: var(--body-text); }
  .intro-heading { left: 640px; top: 746px; width: 420px; }
  .intro-copy { left: 640px; top: 874px; width: 460px; }
  .btn-outline { border: 2px solid var(--brand-red); color: var(--brand-red); border-radius: 26px; display: flex; align-items: center; justify-content: center; font-size: 14px; font-weight: 500; text-transform: uppercase; }
  .intro-cta { left: 640px; top: 1006px; width: 158px; height: 50px; }

  /* Video section */
  .video-band { left: 0; top: 1168px; width: 1200px; height: 630px; background: var(--light-grey); }
  .laptop-lid { left: 396px; top: 1248px; width: 408px; height: 248px; background: #2e2e2e; border-radius: 10px 10px 0 0; }
  .laptop-screen { left: 416px; top: 1268px; width: 368px; height: 212px; background: #a50e14; }
  .laptop-base { left: 344px; top: 1492px; width: 512px; height: 14px; background: linear-gradient(180deg, #4a4a4a, #1e1e1e); border-radius: 0 0 18px 18px / 0 0 12px 12px; }
  .laptop-title { left: 416px; top: 1282px; width: 368px; font-family: "Lato", Arial, sans-serif; font-weight: 300; font-size: 50px; line-height: 60px; color: var(--white); }
  .laptop-sub { left: 416px; top: 1362px; width: 368px; font-family: "Lato", Arial, sans-serif; font-weight: 300; font-size: 27px; line-height: 36px; color: var(--white); }
  .laptop-small { left: 416px; top: 1446px; width: 368px; font-size: 11px; color: #f3c9cb; }
  .video-copy { left: 140px; top: 1570px; width: 920px; text-align: center; font-size: 14px; line-height: 28px; color: #444; }
  .video-cta { left: 504px; top: 1668px; width: 192px; height: 50px; font-size: 14px; }

  /* Services section */
  .services-heading { left: 100px; top: 1886px; width: 520px; }
  .services-copy { left: 100px; top: 1984px; width: 560px; }
  .services-cta { left: 100px; top: 2144px; width: 158px; height: 50px; }
  .pair-back { left: 724px; top: 1864px; width: 188px; height: 392px; }
  .pair-front { left: 888px; top: 1848px; width: 208px; height: 408px; }
  .pair-speaker { height: 4px; border-radius: 2px; background: #9a9a9e; }
  .app-header { height: 40px; background: var(--screen-red); color: var(--white); font-family: "Lato", Arial, sans-serif; font-size: 15px; display: flex; align-items: center; justify-content: center; }
  .map-area { left: 736px; top: 1952px; width: 164px; height: 160px; background: linear-gradient(135deg, #f4f4f4, #dcdcdc); }
  .app-tiny { font-size: 9px; color: var(--ink); }
  .app-bar { height: 22px; background: var(--screen-red); color: var(--white); font-size: 8px; display: flex; align-items: center; justify-content: center; }
  .glasses-area { left: 906px; top: 1936px; width: 172px; height: 92px; background: radial-gradient(ellipse at 50% 55%, #6f7a5e 0%, #c9c4b5 60%, #f4f4f4 100%); }
  .found-title { left: 900px; top: 2034px; width: 184px; font-family: "Playfair Display", Georgia, serif; font-weight: 700; font-size: 15px; line-height: 18px; color: var(--ink); }
  .product-name { left: 900px; top: 2094px; width: 184px; font-size: 11px; font-weight: 500; color: var(--ink); }
  .product-copy { left: 906px; top: 2112px; width: 172px; font-size: 7px; line-height: 10px; color: #444; }

  /* Call to action band */
  .cta-band { left: 0; top: 2254px; width: 1200px; height: 410px; background: var(--brand-red); }
  .cta-title { left: 0; top: 2312px; width: 1200px; text-align: center; font-family: "Lato", Arial, sans-serif; font-weight: 700; font-size: 28px; color: var(--white); }
  .cta-rule { left: 552px; top: 2376px; width: 96px; height: 2px; background: var(--white); }
  .cta-copy { left: 110px; top: 2426px; width: 980px; text-align: center; font-size: 13px; line-height: 24px; color: var(--white); }
  .cta-button { left: 490px; top: 2546px; width: 220px; height: 48px; border-radius: 24px; background: var(--white); color: var(--brand-red); font-size: 14px; font-weight: 500; text-transform: uppercase; display: flex; align-items: center; justify-content: center; }

  /* Footer */
  .brand--dark { left: 0; top: 2728px; width: 1200px; justify-content: center; color: var(--brand-red); font-size: 34px; }
  .brand--dark .brand-mark { background: var(--brand-red); width: 46px; height: 46px; }
  .footer-nav { left: 100px; top: 2844px; width: 1000px; display: flex; justify-content: center; gap: 30px; font-size: 16px; color: var(--ink); text-transform: uppercase; }
  .footer-rule { left: 100px; top: 2906px; width: 1000px; height: 2px; background: var(--rule); }
  .copyright { left: 100px; top: 2944px; font-size: 13px; color: var(--ink); }
  .social-list { left: 906px; top: 2936px; display: flex; gap: 8px; }
  .social-dot { width: 32px; height: 32px; border: 2px solid var(--ink); border-radius: 50%; }
</style>
</head>
<body>

  <!-- Header and hero -->
  <div class="abs hero" role="img" aria-label="Blurred café photograph of a hand holding a smartphone"></div>
  <div class="abs device hero-phone"></div>
  <div class="abs screen hero-screen"></div>
  <p class="abs center hero-screen-name">TRADELUME</p>
  <p class="abs center hero-screen-copy">WE SERVICE TO THE<br>RETAIL AND SHOPPING<br>INDUSTRIES</p>

  <div class="abs brand brand--light"><span class="brand-mark"></span>TRADELUME</div>
  <nav class="abs main-nav"><span>Home</span><span>Products</span><span>Resources</span><span>Support</span></nav>
  <div class="abs btn-ghost-light">GET STARTED</div>

  <h1 class="abs hero-title">TRADELUME</h1>
  <p class="abs hero-lede">We are an Australian based application building technology company.</p>
  <div class="abs btn-solid hero-cta">More Info</div>
  <svg class="abs hero-arrows" width="56" height="36" viewBox="0 0 56 36" aria-hidden="true">
    <polyline points="16,4 4,18 16,32" fill="none" stroke="#ffffff" stroke-width="2.5"/>
    <polyline points="40,4 52,18 40,32" fill="none" stroke="#ffffff" stroke-width="2.5"/>
  </svg>

  <!-- Intro: three phones -->
  <div class="abs device trio-left"></div>
  <div class="abs trio-left-screen" role="img" aria-label="Illustration of a hand holding a phone with an in-store map"></div>
  <div class="abs device trio-right"></div>
  <div class="abs screen trio-right-screen"></div>
  <div class="abs trio-car" role="img" aria-label="Illustration of a car"></div>
  <p class="abs center trio-right-name">tradelume</p>
  <p class="abs center trio-right-copy">We service to the retail and shopping industries, IoT firms etc.</p>
  <div class="abs device trio-center"></div>
  <div class="abs trio-center-screen"></div>
  <p class="abs center trio-center-small" style="top:906px">Entry to exit engagement<br>Map, promote and profile live in store</p>
  <p class="abs center trio-center-name">tradelume</p>
  <p class="abs center trio-center-small" style="top:992px">Navigation and in-store analytics<br>Indoor micro-location shopping</p>

  <h2 class="abs section-heading intro-heading">We are an Australian based application building technology company.</h2>
  <p class="abs section-copy intro-copy">Nemo enim ipsam voluptatem quia voluptas sit aspernatur aut odit aut fugit, sed quia consequuntur magni dolores eos qui ratione voluptatem sequi nesciunt. Neque porro quisquam est, qui dolorem ipsum quia dolor sit amet, consectetur, adipisci velit, sed.</p>
  <div class="abs btn-outline intro-cta">Buind an app</div>

  <!-- Video -->
  <div class="abs video-band"></div>
  <div class="abs laptop-lid"></div>
  <svg class="abs" style="left:596px;top:1252px" width="8" height="8" viewBox="0 0 8 8" aria-hidden="true"><circle cx="4" cy="4" r="3" fill="#555"/></svg>
  <div class="abs laptop-screen"></div>
  <div class="abs laptop-base"></div>
  <p class="abs center laptop-title">Tradelume</p>
  <p class="abs center laptop-sub">Real-time Shopping<br>Online Experiences</p>
  <p class="abs center laptop-small">Bridging online and real-time shopping</p>
  <svg class="abs" style="left:572px;top:1348px" width="56" height="56" viewBox="0 0 56 56" aria-hidden="true">
    <circle cx="28" cy="28" r="26" fill="none" stroke="#ffffff" stroke-width="3"/>
    <polygon points="22,16 40,28 22,40" fill="#ffffff"/>
  </svg>
  <p class="abs video-copy">Sed ut perspiciatis unde omnis iste natus error sit voluptatem accusantium doloremque laudantium, totam rem aperiam, eaque ipsa quae ab illo inventore veritatis et quasi architecto beatae vitae dicta sunt explicabo.</p>
  <div class="abs btn-solid video-cta">Mapping options</div>

  <!-- Services -->
  <h2 class="abs section-heading services-heading">We service to the retail and shopping industries, IoT firms etc.</h2>
  <p class="abs section-copy services-copy">Nemo enim ipsam voluptatem quia voluptas sit aspernatur aut odit aut fugit, sed quia conse quuntur magni dolores eos qui ratione voluptatem sequi nesciunt. Neque porro quisquam est, qui dolorem ipsum quia dolor sit amet, consectetur, adipisci velit, sed. quia non numquam eius modi tem pora incidunt ut labore et dolore magnam. Sed quia conse quuntur magni dolo res eos qui ratione voluptatem sequi nesciunt.</p>
  <div class="abs btn-outline services-cta">Buind an app</div>

  <!-- Back phone: in-store map -->
  <div class="abs device device--silver pair-back"></div>
  <div class="abs pair-speaker" style="left:800px;top:1890px;width:36px"></div>
  <div class="abs screen" style="left:736px;top:1908px;width:164px;height:320px"></div>
  <div class="abs app-header" style="left:736px;top:1908px;width:164px">tradelume</div>
  <div class="abs map-area" role="img" aria-label="In-store floor map"></div>
  <svg class="abs" style="left:744px;top:1990px" width="30" height="42" viewBox="0 0 30 42" aria-hidden="true">
    <path d="M15 1 C7 1 1 7 1 15 C1 25 15 41 15 41 C15 41 29 25 29 15 C29 7 23 1 15 1 Z" fill="#e0262d"/>
    <circle cx="15" cy="15" r="6" fill="#ffffff"/>
  </svg>
  <p class="abs app-tiny" style="left:806px;top:2128px">12 metres to go</p>
  <p class="abs app-tiny" style="left:744px;top:2166px;width:148px;display:flex;justify-content:space-between"><span>GO</span><span>SEARCH</span><span></span></p>
  <div class="abs app-bar" style="left:736px;top:2196px;width:164px">30% off countdown - 15.02 minutes</div>

  <!-- Front phone: product search -->
  <div class="abs device device--silver pair-front"></div>
  <div class="abs pair-speaker" style="left:972px;top:1870px;width:40px"></div>
  <div class="abs screen" style="left:900px;top:1888px;width:184px;height:340px"></div>
  <div class="abs app-header" style="left:900px;top:1888px;width:184px">tradelume</div>
  <div class="abs glasses-area" role="img" aria-label="Product photograph of aviator sunglasses"></div>
  <p class="abs center found-title">Found what you're<br>looking for?</p>
  <p class="abs app-tiny" style="left:910px;top:2078px;width:164px;display:flex;justify-content:space-between;font-size:8px"><span>GO</span><span>SEARCH</span><span>SAVE</span></p>
  <p class="abs center product-name">LUMEN AVIATORS</p>
  <p class="abs product-copy">Classic metal frames with polarised lenses, light and built for all day wear in any weather.</p>
  <div class="abs app-bar" style="left:900px;top:2196px;width:184px">30% off countdown - 14.30 minutes to go</div>

  <!-- Call to action -->
  <div class="abs cta-band"></div>
  <h2 class="abs cta-title">Ready to get started?</h2>
  <div class="abs cta-rule"></div>
  <p class="abs cta-copy">Nemo enim ipsam voluptatem quia voluptas sit aspernatur aut odit aut fugit, sed quia consequuntur magni dolores eos qui ratione voluptatem sequi nesciunt. Neque porro quisquam est, qui dolorem ipsum quia dolor sit amet, consectetur, adipisci velit, sed quia non numquam eius modi tempora incidunt ut labore et dolore magnam aliquam quaerat voluptatem.</p>
  <div class="abs cta-button">Get started with us</div>

  <!-- Footer -->
  <div class="abs brand brand--dark"><span class="brand-mark"></span>TRADELUME</div>
  <nav class="abs footer-nav">
    <span>Home</span><span>|</span><span>Products</span><span>|</span><span>Resources</span><span>|</span><span>Support</span><span>|</span><span>News</span><span>|</span><span>Jobs</span><span>|</span><span>Contact us</span>
  </nav>
  <div class="abs footer-rule"></div>
  <p class="abs copyright">Copyrights © 2017 Tradelume. All Rights Reserved</p>
  <div class="abs social-list" aria-label="Social links">
    <span class="social-dot"></span><span class="social-dot"></span><span class="social-dot"></span><span class="social-dot"></span><span class="social-dot"></span>
  </div>

</body>
</html>
```